Modern Business Card

Modern professional business card with more than just logo and demographic info. Something memorable.

We are a trendy/modern chiropractic group with an emphasis on neurology, hence the minimalist-type brain logo. We want to convey that modern and technical aspect with professionalism and the elite nature of our practice environment.

```html
<!DOCTYPE html>
<html lang="en">
<head>
<meta charset="UTF-8">
<title>Keystone Chiropractic – Business Card</title>
<link href="https://fonts.googleapis.com/css2?family=Cinzel:wght@400;600&family=Jost:wght@400;500&display=swap" rel="stylesheet">
<style>
  :root {
    --page-bg: #d9d9da;
    --card-bg: #141416;
    --card-edge: #2f5fae;
    --brand-blue: #3f7fd6;
    --text-light: #f2f2f2;
    --text-muted: #c9c9c9;
    --emboss-grey: #3a3a3d;
  }
  * { box-sizing: border-box; margin: 0; padding: 0; }
  html, body { width: 1200px; height: 800px; overflow: hidden; }
  body {
    background: var(--page-bg);
    display: flex;
    align-items: center;
    justify-content: space-between;
    padding: 0 40px;
    font-family: "Jost", Arial, sans-serif;
  }
  .card {
    position: relative;
    width: 540px;
    height: 308px;
    background: var(--card-bg);
    border-radius: 18px;
    box-shadow: 0 0 0 2px var(--card-edge), 0 14px 30px rgba(0,0,0,0.35);
    color: var(--text-light);
  }

  /* Front */
  .brand {
    position: absolute;
    top: 48px;
    left: 210px;
    display: flex;
    align-items: center;
    gap: 12px;
  }
  .brand-mark {
    width: 30px; height: 30px;
    background: var(--brand-blue);
  }
  .brand-name {
    font-family: "Cinzel", Georgia, serif;
    font-weight: 400;
    font-size: 24px;
    line-height: 1.05;
    letter-spacing: 1px;
    color: var(--text-light);
  }
  .divider {
    position: absolute;
    top: 148px;
    left: 40px;
    right: 40px;
    height: 1px;
    background: var(--text-light);
  }
  .person {
    position: absolute;
    top: 168px;
    left: 40px;
  }
  .person-name {
    font-family: "Cinzel", Georgia, serif;
    font-weight: 600;
    font-size: 19px;
    letter-spacing: 1px;
    color: var(--brand-blue);
  }
  .person-title {
    font-family: "Cinzel", Georgia, serif;
    font-size: 11px;
    letter-spacing: 1.5px;
    color: var(--text-muted);
    margin-top: 2px;
  }
  .person-rule {
    width: 120px;
    height: 1px;
    background: var(--text-light);
    margin: 8px 0 8px;
  }
  .contact-list { list-style: none; }
  .contact-list li {
    display: flex;
    align-items: center;
    gap: 8px;
    font-size: 12px;
    line-height: 17px;
    color: var(--text-light);
  }
  .contact-list svg { width: 10px; height: 10px; fill: var(--brand-blue); flex: none; }
  .address {
    position: absolute;
    right: 40px;
    bottom: 40px;
    text-align: right;
    font-size: 12px;
    line-height: 18px;
    color: var(--text-light);
  }

  /* Back */
  .card-back {
    display: flex;
    align-items: center;
    justify-content: center;
  }
  .back-brand {
    display: flex;
    align-items: center;
    gap: 14px;
  }
  .back-brand .brand-mark { width: 36px; height: 36px; background: var(--emboss-grey); }
  .back-brand .brand-name { font-size: 30px; color: var(--emboss-grey); }
</style>
</head>
<body>
  <section class="card card-front">
    <div class="brand">
      <span class="brand-mark"></span>
      <span class="brand-name">Keystone<br>Chiropractic</span>
    </div>

    <div class="divider"></div>

    <div class="person">
      <p class="person-name">Daniel Reyes</p>
      <p class="person-title">President</p>
      <div class="person-rule"></div>
      <ul class="contact-list">
        <li>
          <svg viewBox="0 0 10 10"><path d="M2 0.5 L3.8 0.5 L4.3 3 L3 3.9 Q4 6 6.1 7 L7 5.7 L9.5 6.2 L9.5 8 Q9.5 9.5 8 9.5 Q0.5 9 0.5 2 Q0.5 0.5 2 0.5Z"/></svg>
          555-204-7731
        </li>
        <li>
          <svg viewBox="0 0 10 10"><path d="M2.5 0 H7.5 V10 H2.5Z M3.3 1 V8 H6.7 V1Z"/></svg>
          555-318-6402
        </li>
        <li>
          <svg viewBox="0 0 10 10"><path d="M1 3 H9 V9 H1Z M3 0.5 H7 V2.5 H3Z"/></svg>
          555-427-9185
        </li>
        <li>
          <svg viewBox="0 0 10 10"><path d="M0.5 2 H9.5 V8.5 H0.5Z M1.3 2.6 L5 5.6 L8.7 2.6Z" fill-rule="evenodd"/></svg>
          hello@keystonechiropractic.com
        </li>
      </ul>
    </div>

    <address class="address" style="font-style: normal;">
      214 Alder Court<br>
      Fairview, Oregon 97024<br>
      www.keystonechiropractic.com
    </address>
  </section>

  <section class="card card-back">
    <div class="back-brand">
      <span class="brand-mark"></span>
      <span class="brand-name">Keystone<br>Chiropractic</span>
    </div>
  </section>
</body>
</html>
```